BOLD & MINIMALIST DESIGN NEEDED

We want a very bold but minimalistic business card design that is impactful and utilizes both sides of the business card. Our current logo is included for your use.

We want bold fonts and good use of negative space. We don't want the logo to overpower the design.

Target Market(s)

Professionals who are building new commercial buildings.

Industry/Entity Type

Construction

Contact Information for Business Card

Name, Title, email, office phone, cell phone, website

Font styles to use
Serif
Sans Serif

Requirements
Must have
• Bold design!

```html
<!DOCTYPE html>
<html lang="en">
<head>
<meta charset="utf-8">
<title>Ridgeline Design + Build — Business Card</title>
<link href="https://fonts.googleapis.com/css2?family=Montserrat:wght@500;600;700;800&display=swap" rel="stylesheet">
<style>
  :root {
    --backdrop: #d9dadc;
    --card: #ffffff;
    --ink: #000000;
    --paper-text: #ffffff;
  }
  * { margin: 0; padding: 0; box-sizing: border-box; }
  html, body {
    width: 1200px;
    height: 900px;
    overflow: hidden;
    background: var(--backdrop);
    font-family: "Montserrat", Arial, sans-serif;
    color: var(--ink);
  }
  .canvas { position: relative; width: 1200px; height: 900px; }

  .card {
    position: absolute;
    width: 513px;
    height: 293px;
    background: var(--card);
    overflow: hidden;
  }

  /* Front */
  .card--front { left: 218px; top: 123px; }
  .front-band {
    position: absolute;
    left: 0; bottom: 0;
    width: 100%;
    height: 73px;
    background: var(--ink);
  }
  .brand-name {
    position: absolute;
    left: 0; width: 100%;
    top: 182px;
    text-align: center;
    font-weight: 800;
    font-size: 33px;
    letter-spacing: 0.5px;
    line-height: 1;
    color: var(--ink);
  }
  .brand-tagline {
    position: absolute;
    left: 0; width: 100%;
    top: 226px;
    text-align: center;
    font-weight: 500;
    font-size: 12.5px;
    letter-spacing: 4px;
    color: var(--paper-text);
  }

  /* Back */
  .card--back { left: 470px; top: 476px; }
  .back-brand {
    position: absolute;
    left: 36px; top: 40px;
    font-weight: 800;
    font-size: 13px;
    letter-spacing: 1px;
    color: var(--ink);
  }
  .holder {
    position: absolute;
    left: 0; width: 100%;
    top: 98px;
    text-align: center;
  }
  .holder-name {
    font-weight: 700;
    font-size: 28px;
    letter-spacing: 1.5px;
    line-height: 1;
  }
  .holder-title {
    margin-top: 8px;
    font-weight: 700;
    font-size: 13px;
    letter-spacing: 1px;
  }
  .contact-list {
    position: absolute;
    left: 0; width: 100%;
    top: 167px;
    list-style: none;
    text-align: center;
    font-weight: 600;
    font-size: 11.5px;
    letter-spacing: 1px;
    line-height: 16.5px;
  }
  .contact-label { margin-right: 8px; }
  .website {
    position: absolute;
    left: 0; width: 100%;
    top: 244px;
    text-align: center;
    font-weight: 600;
    font-size: 11.5px;
    letter-spacing: 1px;
  }
</style>
</head>
<body>
<main class="canvas">
  <section class="card card--front" aria-label="Card front">
    <div class="brand-name">RIDGELINE</div>
    <div class="front-band"></div>
    <div class="brand-tagline">DESIGN + BUILD</div>
  </section>

  <section class="card card--back" aria-label="Card back">
    <div class="back-brand">RIDGELINE</div>
    <div class="holder">
      <h1 class="holder-name">DANA PORTER</h1>
      <p class="holder-title">PROJECT MANAGER</p>
    </div>
    <ul class="contact-list">
      <li><span class="contact-label">P :</span>+1 (555) 014-2870</li>
      <li><span class="contact-label">M :</span>+6015 0123 4567</li>
      <li><span class="contact-label">E :</span>DANA@RIDGELINE.COM</li>
    </ul>
    <p class="website">WWW.RIDGELINE.COM</p>
  </section>
</main>
</body>
</html>
```